Business card design for a dynamic IT consulting company

We need a business card design for a young firm, specialized in the Telecommunications/Consulting industry. The name of the company is Quindor and Partners Business Consulting Ltd. (Short name: Quindor and Partnes)
Quindor = solve read reverse, so we aim to be uncomplicated and solution-oriented. The small pipe in our logo is also related to the word solve. So we need a new business card design, which is simple, eye catching and something non traditional (I would probably prefer a square shaped design rather than a rectangle, but open for suggestions). Attached our logo.

Target Market(s)

Usually our customers are Tier1 Telecoms providers (Q-Netra, Palorix, etc) and their executives.

Industry/Entity Type

Business

Contact Information for Business Card

Name: Bence Tolnavari
Email: b.tolnavari@quindor.hu
Web: www.quindor.hu
Mobile: +36 30 518 2769
Title: Managing Director

Optional:
Company name: Quindor and Partners Ltd.
Address: 1087 Budapest, Tolvenka str. 28/C, Hungary

Font styles to use
Other font styles liked:
• helveticaneue_medium, Prime Regular are used now.

Colors

Designer to choose colors to be used in the design.

Requirements
Must have
• I would like to have a 2 sided design.
Nice to have
• I thought if we make the logo a bit bigger (without the company name), that could go to the back with the company name below. I though, if the pipe in the logo is somehow touchable on the business card, would be nice and unique.

```html
<!DOCTYPE html>
<html lang="en">
<head>
<meta charset="utf-8">
<title>Quindor and Partners – Business Card</title>
<link rel="stylesheet" href="https://fonts.googleapis.com/css2?family=Work+Sans:wght@400;500&family=Saira+Condensed:wght@600&family=Chakra+Petch:ital,wght@1,500&display=swap">
<style>
  :root {
    --backdrop: #1b1b1c;
    --card: #262627;
    --ink: #f1f1f1;
    --muted: #d8d8d8;
    --blue: #1a9fe0;
    --magenta: #b0308f;
  }
  * { box-sizing: border-box; margin: 0; padding: 0; }
  html, body {
    width: 1200px; height: 900px; overflow: hidden;
    background: radial-gradient(ellipse at 60% 40%, #2c2c2d 0%, var(--backdrop) 70%);
    font-family: "Work Sans", Arial, sans-serif;
    color: var(--ink);
  }
  .canvas {
    width: 1200px; height: 900px;
    display: flex; flex-direction: column; align-items: center; justify-content: center;
    gap: 40px;
  }
  .card {
    position: relative;
    width: 700px; height: 400px;
    background: var(--card);
    box-shadow: 0 18px 40px rgba(0,0,0,.55);
    overflow: hidden;
  }
  .card__band {
    position: absolute; left: 0; right: 0; bottom: 0; height: 8px;
    background: var(--blue);
  }

  /* Front */
  .brand {
    position: absolute; left: 0; right: 0; top: 140px;
    text-align: center;
  }
  .brand__name {
    font-weight: 500; font-size: 52px; letter-spacing: 1px; color: var(--ink);
  }
  .front__web {
    position: absolute; left: 0; right: 0; bottom: 42px;
    text-align: center; font-size: 17px; letter-spacing: 3px; color: var(--muted);
  }

  /* Back */
  .person {
    position: absolute; right: 372px; top: 142px; text-align: right;
  }
  .person__name {
    font-family: "Saira Condensed", "Arial Narrow", sans-serif;
    font-weight: 600;
    font-size: 44px; line-height: 1; color: var(--blue); text-transform: uppercase;
  }
  .person__title {
    margin-top: 8px; font-size: 17px; letter-spacing: 1px; text-transform: uppercase; color: var(--ink);
  }
  .divider {
    position: absolute; left: 350px; top: 138px; width: 2px; height: 84px; background: var(--magenta);
  }
  .contacts {
    position: absolute; left: 378px; top: 140px;
    list-style: none; display: flex; flex-direction: column; gap: 6px;
    font-size: 17px; letter-spacing: .5px; color: var(--ink);
  }
  .contacts li { display: flex; align-items: center; gap: 14px; }
  .contacts svg { width: 16px; height: 16px; flex: none; }
  .company-line {
    position: absolute; left: 48px; bottom: 40px;
    font-size: 16px; letter-spacing: .5px; color: var(--ink);
  }
  .company-line__name {
    font-family: "Chakra Petch", Arial, sans-serif; font-style: italic; font-weight: 500;
    color: var(--blue); text-transform: uppercase; font-size: 18px;
  }
</style>
</head>
<body>
<main class="canvas">
  <section class="card card--front">
    <div class="brand">
      <span class="brand__name">Quindor and Partners</span>
    </div>
    <p class="front__web">www.quindor.hu</p>
    <div class="card__band"></div>
  </section>

  <section class="card card--back">
    <div class="person">
      <h1 class="person__name">Bence Tolnavari</h1>
      <p class="person__title">Managing Director</p>
    </div>
    <div class="divider"></div>
    <ul class="contacts">
      <li>
        <svg viewBox="0 0 16 16" aria-hidden="true"><path fill="var(--blue)" d="M3.5 1.5l2.5 0 1 3.5-1.6 1.2a8 8 0 0 0 4.4 4.4L11 9l3.5 1v2.5c0 1-1 1.8-2 1.6A12 12 0 0 1 1.9 3.5c-.2-1 .6-2 1.6-2z"/></svg>
        +36 30 518 2769
      </li>
      <li>
        <svg viewBox="0 0 16 16" aria-hidden="true"><rect x="1" y="3" width="14" height="10" fill="var(--blue)"/><path d="M1 3l7 6 7-6" fill="none" stroke="var(--card)" stroke-width="1.3"/></svg>
        b.tolnavari@quindor.hu
      </li>
      <li>
        <svg viewBox="0 0 16 16" aria-hidden="true"><g fill="none" stroke="var(--blue)" stroke-width="1.3"><circle cx="8" cy="8" r="6.5"/><ellipse cx="8" cy="8" rx="3" ry="6.5"/><path d="M1.5 8h13M2.5 4.8h11M2.5 11.2h11"/></g></svg>
        www.quindor.hu
      </li>
    </ul>
    <p class="company-line"><span class="company-line__name">Quindor and Partners Ltd:</span> 1087 Budapest, Tolvenka str. 28/C, Hungary</p>
    <div class="card__band"></div>
  </section>
</main>
</body>
</html>
```